Travel Agency Website - Simple General

Need a 7 page simple design that is pretty repetitive. Need to be able to load quickly that is SEO optimized. Trying to give ideas on what they can do, be personal as we are local, but at the same time come across as professional and get information easily with little burden.

- Landing Page
- Brimwell Vacations Page
- Family Trips
- Road Trips from Texas
- Other Destinations
- About Us Page
- Contact Us Page

Target Market(s)

Families

Coding

Coded - Design and coding required

Number of Pages Required

5+ page

Colors

Designer to choose colors to be used in the design.

Requirements
Must have
• Like it to flow easily with our logo. Use that for colors, etc.

```html
<!DOCTYPE html>
<html lang="en">
<head>
<meta charset="utf-8">
<title>Contact Us – Meadowlark Trail Travel Co.</title>
<link href="https://fonts.googleapis.com/css2?family=Poppins:wght@400;500;600&family=Oswald:wght@500;600&display=swap" rel="stylesheet">
<style>
:root{
  --cream:#fcf8f2;
  --teal-dark:#0b3d50;
  --teal-mid:#2c8a8a;
  --gold:#c0954a;
  --ink:#123f50;
  --field-border:#c9ccd0;
  --white:#ffffff;
}
*{box-sizing:border-box;margin:0;padding:0}
html,body{width:1200px;height:927px;overflow:hidden;background:var(--cream);font-family:'Poppins',sans-serif;color:var(--ink)}
.page{position:relative;width:1200px;height:927px;overflow:hidden}
.hero-map{position:absolute;left:0;top:0;width:1200px;height:340px;
  background:radial-gradient(ellipse at 85% 25%,#cfe0e6 0,#e4ece9 30%,rgba(252,248,242,0) 60%),
             linear-gradient(180deg,#eee9dc 0%,#f1ece2 55%,var(--cream) 100%);}
.brand{position:absolute;left:150px;top:36px;display:flex;align-items:center;gap:8px}
.brand-dot{width:14px;height:14px;border-radius:50%;background:var(--teal-mid)}
.brand-name{font-size:17px;font-weight:600;color:var(--teal-dark)}
.nav{position:absolute;right:150px;top:33px;display:flex;align-items:center;gap:22px;font-size:11px;font-weight:500;text-transform:uppercase;letter-spacing:.2px}
.nav a{color:var(--ink);text-decoration:none;position:relative}
.nav a.active{color:var(--gold)}
.nav a.active::after{content:"";position:absolute;left:50%;transform:translateX(-50%);top:21px;width:29px;height:2.5px;border-radius:2px;background:var(--gold)}
.intro{position:absolute;left:0;width:1200px;top:148px;text-align:center}
.intro h1{font-family:'Oswald',sans-serif;font-weight:600;font-size:32px;letter-spacing:.5px;color:var(--teal-dark)}
.intro p{margin:10px auto 0;width:430px;font-size:12px;line-height:19px}
.form{position:absolute;left:421px;top:267px;width:360px}
.field{position:relative;height:41px;margin-bottom:7.5px;background:var(--white);border:1px solid var(--field-border);border-radius:5px;display:flex;align-items:center}
.field .icon{width:32px;display:flex;justify-content:center;border-right:1px solid #e3e3e3;height:24px;align-items:center}
.field label,.message label{font-family:'Oswald',sans-serif;font-weight:500;font-size:14px;color:var(--teal-dark);padding-left:14px;letter-spacing:.2px}
.field .chev{position:absolute;right:20px;top:28px}
.message{height:123px;background:var(--white);border:1px solid var(--field-border);border-radius:5px;padding-top:12px;padding-left:2px}
.submit{margin-top:10px;width:360px;height:41px;border:none;border-radius:5px;background:var(--gold);color:var(--white);font-family:'Oswald',sans-serif;font-weight:500;font-size:14px;letter-spacing:.4px}
.footer{position:absolute;left:0;top:637px;width:1200px;height:290px}
.footer svg.wave{position:absolute;left:0;top:0}
.footer-contact{position:absolute;left:150px;top:144px;color:var(--white);font-size:12px;font-weight:500}
.footer-contact li{list-style:none;display:flex;align-items:center;gap:7px;margin-bottom:2px}
.badge{width:19px;height:19px;border-radius:50%;background:var(--gold);display:flex;align-items:center;justify-content:center}
.footer-brand{position:absolute;left:0;width:1200px;top:143px;display:flex;justify-content:center;align-items:center;gap:8px}
.footer-brand .brand-dot{background:var(--gold)}
.footer-brand .brand-name{color:var(--white)}
.social{position:absolute;right:150px;top:145px;display:flex;gap:3px}
.social span{width:31px;height:31px;border-radius:50%;background:var(--gold);display:block}
.divider{position:absolute;left:150px;top:243px;width:900px;height:1px;background:rgba(255,255,255,.15)}
.copyright{position:absolute;left:0;width:1200px;top:258px;text-align:center;color:var(--white);font-size:10.5px}
.to-top{position:absolute;left:1101px;top:229px;width:28px;height:28px;border-radius:50%;background:var(--teal-mid);display:flex;align-items:center;justify-content:center}
</style>
</head>
<body>
<div class="page">
  <div class="hero-map" role="img" aria-label="Faded street map background with a plane and dotted flight path"></div>

  <header>
    <div class="brand"><span class="brand-dot"></span><span class="brand-name">Meadowlark Trail</span></div>
    <nav class="nav">
      <a href="#" aria-label="Home"><svg width="12" height="11" viewBox="0 0 12 11"><path d="M6 0 0 5h1.5v6h3.5V7.5h2V11h3.5V5H12z" fill="#123f50"/></svg></a>
      <a href="#">Brimwell Vacations</a>
      <a href="#">Family Trips</a>
      <a href="#">Texas Road Trips</a>
      <a href="#">Other Destinations</a>
      <a href="#">About Us</a>
      <a href="#" class="active">Contact Us</a>
    </nav>
  </header>

  <section class="intro">
    <h1>GET IN TOUCH</h1>
    <p>We'd love to help plan your next family adventure. Please fill out the details below, and we'll be in wander with you soon!</p>
  </section>

  <form class="form">
    <div class="field">
      <span class="icon"><svg width="8" height="9" viewBox="0 0 8 9"><circle cx="4" cy="2.3" r="2.2" fill="#0b3d50"/><path d="M0 9c0-3 1.8-4 4-4s4 1 4 4z" fill="#0b3d50"/></svg></span>
      <label>NAME</label>
      <svg class="chev" width="6" height="9" viewBox="0 0 6 9"><path d="M1 1l3.5 3.5L1 8" stroke="#555" stroke-width="1.2" fill="none"/></svg>
    </div>
    <div class="field">
      <span class="icon"><svg width="9" height="7" viewBox="0 0 9 7"><rect width="9" height="7" rx="1" fill="#0b3d50"/><path d="M0 1l4.5 3L9 1" stroke="#fff" stroke-width=".9" fill="none"/></svg></span>
      <label>EMAIL</label>
    </div>
    <div class="field">
      <span class="icon"><svg width="9" height="9" viewBox="0 0 9 9"><path d="M2 0l1.5 2-1 1.2c.6 1.3 1.5 2.2 2.8 2.8l1.2-1L9 6.5 7.8 8.6C3.8 8.4.6 5.2.4 1.2z" fill="#0b3d50"/></svg></span>
      <label>PHONE</label>
    </div>
    <div class="message"><label>ANY DETAILS YOU WANT US TO KNOW?</label></div>
    <button class="submit" type="button">SEND INQUIRY</button>
  </form>

  <footer class="footer">
    <svg class="wave" width="1200" height="290" viewBox="0 0 1200 290">
      <path d="M0 103 Q180 60 380 60 Q520 60 600 2 Q680 60 820 60 Q1020 60 1200 103" fill="none" stroke="#2c8a8a" stroke-width="1.2"/>
      <path d="M0 112 Q180 68 380 68 Q520 68 600 10 Q680 68 820 68 Q1020 68 1200 112 V290 H0 Z" fill="#0b3d50"/>
    </svg>
    <ul class="footer-contact">
      <li><span class="badge"><svg width="9" height="9" viewBox="0 0 9 9"><path d="M2 0l1.5 2-1 1.2c.6 1.3 1.5 2.2 2.8 2.8l1.2-1L9 6.5 7.8 8.6C3.8 8.4.6 5.2.4 1.2z" fill="#fff"/></svg></span>555.010.2468</li>
      <li><span class="badge"><svg width="9" height="7" viewBox="0 0 9 7"><rect width="9" height="7" rx="1" fill="#fff"/><path d="M0 1l4.5 3L9 1" stroke="#c0954a" stroke-width=".9" fill="none"/></svg></span>hello@meadowlarktrail.com</li>
    </ul>
    <div class="footer-brand"><span class="brand-dot"></span><span class="brand-name">Meadowlark Trail</span></div>
    <div class="social"><span aria-label="Social profile one"></span><span aria-label="Social profile two"></span></div>
    <div class="divider"></div>
    <p class="copyright">© 2026 MeadowlarkTrail / Alll Rights Reserved</p>
    <a class="to-top" href="#" aria-label="Back to top"><svg width="7" height="5" viewBox="0 0 7 5"><path d="M1 4l2.5-2.5L6 4" stroke="#fff" stroke-width="1.3" fill="none"/></svg></a>
  </footer>
</div>
</body>
</html>
```